its a new company based in Christchurch new Zealand building computers ,repairs, upgrades and anything computers for the general public,i like bright happy colours like yellows, greens reds anything that stands out and it needs to communicant trust and security towards my new company,i have no logo yet,

Target Market(s)

target market of all ages

Industry/Entity Type

Building

Contact Information for Business Card

Byte Harbour Limited,ph-0218847261,email-tidelark77@mailvesta.test,14c marlowe cres,fenwick

```html
<!DOCTYPE html>
<html lang="en">
<head>
<meta charset="utf-8">
<title>Byte Harbour Limited – Business Card</title>
<link href="https://fonts.googleapis.com/css2?family=Open+Sans:wght@400;600;700&display=swap" rel="stylesheet">
<style>
  :root {
    --backdrop: #e6e8eb;
    --card-white: #ffffff;
    --card-shade: #e9eaec;
    --brand-blue: #3f8fd0;
    --name-blue: #1f8fcf;
    --ink: #333a40;
    --band-slate: #5b74ad;
    --band-sky: #49b8ea;
    --icon-blue: #3f6fb5;
  }
  * { margin: 0; padding: 0; box-sizing: border-box; }
  html, body {
    width: 1200px;
    height: 899px;
    overflow: hidden;
    background: var(--backdrop);
    font-family: "Open Sans", Arial, sans-serif;
  }
  .sheet {
    position: relative;
    width: 1200px;
    height: 899px;
  }
  .card {
    position: absolute;
    left: 250px;
    width: 700px;
    height: 400px;
    background: radial-gradient(ellipse at 45% 40%, var(--card-white) 40%, var(--card-shade) 100%);
    box-shadow: 0 6px 18px rgba(0,0,0,0.18);
    overflow: hidden;
  }
  .card--front { top: 30px; }
  .card--back { top: 469px; }

  .brand {
    position: absolute;
    display: flex;
    align-items: center;
    gap: 12px;
    color: var(--brand-blue);
    font-weight: 700;
    line-height: 1.05;
  }
  .brand__dot {
    flex: none;
    border-radius: 50%;
    background: var(--brand-blue);
  }
  .card--front .brand {
    left: 50%;
    top: 50%;
    transform: translate(-50%, -50%);
    font-size: 34px;
  }
  .card--front .brand__dot { width: 30px; height: 30px; }
  .card--back .brand {
    left: 46px;
    top: 58px;
    font-size: 26px;
  }
  .card--back .brand__dot { width: 24px; height: 24px; }

  .holder {
    position: absolute;
    left: 46px;
    top: 150px;
  }
  .holder__name {
    color: var(--name-blue);
    font-weight: 600;
    font-size: 21px;
  }
  .holder__role {
    color: var(--ink);
    font-size: 19px;
    margin-top: 2px;
  }

  .contact {
    position: absolute;
    left: 452px;
    top: 52px;
    list-style: none;
    color: var(--ink);
    font-size: 15px;
    line-height: 22px;
  }
  .contact__item {
    display: flex;
    align-items: center;
    gap: 8px;
  }
  .contact__item svg {
    width: 13px;
    height: 13px;
    flex: none;
    fill: var(--icon-blue);
  }
  .contact__item--plain { padding-left: 21px; }

  .wave {
    position: absolute;
    left: 0;
    bottom: 0;
    width: 700px;
    height: 400px;
  }
</style>
</head>
<body>
<main class="sheet">
  <section class="card card--front" aria-label="Card front">
    <div class="brand"><span class="brand__dot"></span><span>Byte Harbour<br>Limited</span></div>
  </section>

  <section class="card card--back" aria-label="Card back">
    <svg class="wave" viewBox="0 0 700 400" aria-hidden="true">
      <path d="M0 400 L0 348 C180 340 420 300 700 160 L700 400 Z" fill="var(--band-slate)"/>
      <path d="M0 344 C190 336 420 296 700 152" fill="none" stroke="var(--band-sky)" stroke-width="5"/>
    </svg>

    <div class="brand"><span class="brand__dot"></span><span>Byte Harbour<br>Limited</span></div>

    <div class="holder">
      <p class="holder__name">Marin Colfax-Dene</p>
      <p class="holder__role">Consultant</p>
    </div>

    <ul class="contact">
      <li class="contact__item contact__item--plain">14c marlowe cres,</li>
      <li class="contact__item contact__item--plain">fenwick</li>
      <li class="contact__item">
        <svg viewBox="0 0 16 16"><rect x="1" y="5" width="14" height="10" rx="1"/><rect x="4" y="1" width="8" height="5"/></svg>
        03 366 2140
      </li>
      <li class="contact__item">
        <svg viewBox="0 0 16 16"><path d="M3 1l3 0 1 4-2 1.5c1 2 2.5 3.5 4.5 4.5L11 9l4 1v3c0 1-1 2-2 2C7 15 1 9 1 3c0-1 1-2 2-2z"/></svg>
        021 884 7261
      </li>
      <li class="contact__item">
        <svg viewBox="0 0 16 16"><path d="M1 3h14v10H1z M1 3l7 6 7-6" stroke="#fff" stroke-width="1"/></svg>
        tidelark77@mailvesta.test
      </li>
      <li class="contact__item">
        <svg viewBox="0 0 16 16"><circle cx="8" cy="8" r="7"/><path d="M1 8h14M8 1c-3 3-3 11 0 14M8 1c3 3 3 11 0 14" stroke="#fff" stroke-width="1" fill="none"/></svg>
        www.byteharbour.test
      </li>
    </ul>
  </section>
</main>
</body>
</html>
```